New Mechanical Maintenance business needs website

New Mechanical Maintenance business in Perth Western Australia needs a nice and easy to navigate website. Showing what we do and how we can be the right fit for other small to medium size business by offering personalized service from our highly skilled team. We deal with both fixed plant repairs like food and chemical processing facilities to heavy equipment like drill rigs, Large boats and earthmoving equipment.

Target Market(s)

Small to medium business to offer personalized services/packages

Industry/Entity Type

e deal with both fixed plant repairs like food and chemical processing facilities to heavy equipment like drill rigs, Large boats and earthmoving equipment.

Coding

Coded - Design and coding required

Number of Pages Required

4 page

Font styles to use
Serif

Colors
0054AA
0677BA
7BADD7
CADEEF
E8F1F8

Requirements
Must have
• A website that is easy to navigate but covers off on the range of services/maintenance we can provide

```html
<!DOCTYPE html>
<html lang="en">
<head>
<meta charset="utf-8">
<title>KWR Maintenance</title>
<link href="https://fonts.googleapis.com/css2?family=Hind:wght@400;500;600&family=Roboto:wght@400;500;700&display=swap" rel="stylesheet">
<style>
:root{
  --ink:#1f1f1f;
  --muted:#6b6b6b;
  --topbar:#e9e9ea;
  --link:#0054aa;
  --btn:#555b61;
  --phone-btn:#3d5580;
  --light:#f2f2f2;
  --slate:#4e5f84;
  --black:#000;
  --white:#fff;
}
*{box-sizing:border-box;margin:0;padding:0}
html,body{width:1200px;height:3781px;overflow:hidden}
body{font-family:"Roboto",sans-serif;color:var(--ink);background:var(--white);position:relative}
.abs{position:absolute}
.heading{font-family:"Hind",sans-serif;font-weight:600}
.topbar{left:0;top:0;width:1200px;height:41px;background:var(--topbar);font-size:13px;color:#555;text-align:center;line-height:41px}
.topbar a{color:var(--link);text-decoration:none}
.hero{left:0;top:41px;width:1200px;height:602px;background:linear-gradient(90deg,#14305e 0%,#324e78 40%,#8a8f94 62%,#c28a55 75%,#5d6a78 100%)}
.brand{display:flex;align-items:center;gap:10px;color:var(--white);font-family:"Hind",sans-serif;font-weight:600;font-size:22px;letter-spacing:3px;line-height:1}
.brand .dot{width:54px;height:54px;border-radius:50%;border:5px solid var(--white)}
.brand small{display:block;font-size:10px;letter-spacing:1.5px;margin-top:3px}
.nav a{position:absolute;color:var(--white);font-size:14px;font-weight:500;text-decoration:none}
.social{width:29px;height:29px;border-radius:50%;background:var(--white)}
.pill{display:flex;align-items:center;justify-content:center;gap:8px;border-radius:30px;background:var(--btn);color:var(--white);font-size:13px;font-weight:700;text-transform:uppercase}
.hero-title{left:110px;top:196px;font-size:47px;line-height:56px;color:var(--white);white-space:nowrap}
.section-title{font-size:37px;color:var(--ink);line-height:1.2}
.about-img{left:110px;top:728px;width:415px;height:372px;background:linear-gradient(135deg,#c8a24a,#3c5f86 45%,#29476c 70%,#d86a2a)}
.badge{left:425px;top:766px;width:138px;height:136px;background:var(--white);box-shadow:0 4px 14px rgba(0,0,0,.2);text-align:center;font-weight:700}
.badge .num{font-size:52px;line-height:1;margin-top:30px;color:#333}
.badge .num span{font-size:16px}
.badge .lbl{font-size:19px;margin-top:6px}
.body-text{font-size:13.5px;line-height:26px;color:var(--muted);text-align:justify}
.services{left:0;top:1188px;width:1200px;height:1120px;background:var(--light)}
.card{width:295px}
.card .ph{height:250px}
.card h3{font-size:15.5px;font-weight:700;margin-top:24px;color:var(--ink);white-space:nowrap}
.card p{width:284px;font-size:14px;line-height:26px;color:var(--muted);text-align:justify;margin-top:14px}
.clients{left:0;top:2308px;width:1200px;height:365px;background:var(--slate);color:var(--white);text-align:center}
.arrow{width:46px;height:46px;border-radius:50%;background:var(--white);color:#333;font-size:18px;line-height:46px;text-align:center}
.tile{position:absolute}
.footer{left:0;top:3462px;width:1200px;height:319px;background:var(--black);color:var(--white)}
.footer h4{position:absolute;top:100px;font-size:14px;font-weight:700}
.footer .list{position:absolute;font-size:13.5px;line-height:26px}
</style>
</head>
<body>

<div class="abs topbar">Call Us Today on <a href="#">+1 (5550) 555 555</a> for a free onsite quotation or email <a href="#">info@kwrmaintenance.com</a></div>

<header class="abs hero" role="img" aria-label="Welder in hard hat and hi-vis vest working on steel in a workshop, blue overlay on left">
  <div class="abs brand" style="left:114px;top:32px"><div class="dot"></div><div>KWR<small>MAINTENANCE</small></div></div>
  <nav class="nav">
    <a style="left:478px;top:31px">Home</a>
    <a style="left:549px;top:31px">About</a>
    <a style="left:623px;top:31px">Services</a>
    <a style="left:710px;top:31px">Work</a>
  </nav>
  <div class="abs social" style="left:789px;top:26px"></div>
  <div class="abs social" style="left:831px;top:26px"></div>
  <div class="abs social" style="left:874px;top:26px"></div>
  <div class="abs pill" style="left:940px;top:19px;width:137px;height:41px;font-weight:500">Contact Us</div>
  <h1 class="abs heading hero-title">Specialists In Engineering,<br>Maintenance &amp; Support<br>Services</h1>
  <div class="abs pill" style="left:110px;top:400px;width:156px;height:42px">Get Started
    <svg width="12" height="12" viewBox="0 0 12 12"><circle cx="6" cy="6" r="6" fill="#fff"/><path d="M5 3l3 3-3 3" stroke="#555b61" stroke-width="1.8" fill="none"/></svg></div>
  <div class="abs pill" style="left:288px;top:400px;width:206px;height:42px;background:var(--phone-btn);font-size:14px;text-transform:none">
    <svg width="30" height="30" viewBox="0 0 30 30"><circle cx="15" cy="15" r="15" fill="#fff"/><path d="M10 9c1-1 2-1 2.5 0l1.2 2c.4.7 0 1.3-.6 1.7-.4.3-.3.8 0 1.3 1 1.5 1.8 2.3 3.2 3.2.5.3 1 .4 1.3 0 .4-.6 1-1 1.7-.6l2 1.2c1 .5 1 1.5 0 2.5-2 2-5 .5-8-2.5s-4.5-6-2.5-8.3z" fill="#333"/></svg>
    +1 (5550) 555 555</div>
</header>

<section>
  <div class="abs about-img" role="img" aria-label="Team of smiling workers in hard hats and hi-vis vests"></div>
  <div class="abs badge"><div class="num">20<span>Yrs</span></div><div class="lbl">EXPERIENCE</div></div>
  <h2 class="abs heading section-title" style="left:618px;top:722px">About Us</h2>
  <p class="abs body-text" style="left:618px;top:783px;width:468px">Lorem ipsum dolor sit amet, consectetur adipiscing elit, sed do eiusmod tempor incididunt ut labore et dolore magna aliqua. Ut enim ad minim veniam, quis nostrud exercitation ullamco laboris nisi ut aliquip ex ea commodo consequat. Duis aute irure dolor in reprehenderit in voluptate velit esse cillum dolore eu fugiat nulla pariatur. Excepteur sint occaecat cupidatat non proident, sunt in culpa qui officia deserunt.</p>
  <p class="abs body-text" style="left:618px;top:953px;width:468px">Lorem ipsum dolor sit amet, consectetur adipiscing elit, sed do eiusmod tempor incididunt ut labore et dolore magna aliqua. Ut enim ad minim veniam, quis nostrud exercitation .</p>
  <div class="abs pill" style="left:618px;top:1057px;width:155px;height:43px">View More
    <svg width="12" height="12" viewBox="0 0 12 12"><circle cx="6" cy="6" r="6" fill="#fff"/><path d="M5 3l3 3-3 3" stroke="#555b61" stroke-width="1.8" fill="none"/></svg></div>
</section>

<section class="abs services">
  <h2 class="abs heading section-title" style="left:110px;top:80px">Services We Offer</h2>
  <div class="abs card" style="left:114px;top:165px"><div class="ph" role="img" aria-label="Technician adjusting gears on machinery" style="background:linear-gradient(135deg,#9aa6b2,#4f5a66 50%,#d9a23a)"></div><h3>Fixed Plant Mechanical &amp; Maintenance</h3><p>Lorem ipsum dolor sit amet, consectetur adipiscing elit, sed do eiusmod tempor incididunt ut labore</p></div>
  <div class="abs card" style="left:453px;top:165px"><div class="ph" role="img" aria-label="High-rise buildings under construction with cranes and excavator" style="background:linear-gradient(180deg,#b9cfe3,#6f7378 60%,#8b6a4e)"></div><h3>Sustaining Capital &amp; Minor Projects</h3><p>Lorem ipsum dolor sit amet, consectetur adipiscing elit, sed do eiusmod tempor incididunt ut labore</p></div>
  <div class="abs card" style="left:792px;top:165px"><div class="ph" role="img" aria-label="Machinist operating a lathe" style="background:linear-gradient(135deg,#5f7a68,#8a8d8e 50%,#3f4346)"></div><h3>Rotating Equipment &amp; On-Site Machining</h3><p>Lorem ipsum dolor sit amet, consectetur adipiscing elit, sed do eiusmod tempor incididunt ut labore</p></div>
  <div class="abs card" style="left:114px;top:583px"><div class="ph" role="img" aria-label="CNC laser cutting sheet metal with sparks" style="background:linear-gradient(135deg,#7b8794,#2f3740 50%,#d88a2c)"></div><h3>Workshop Fabrication &amp; CNC Machining</h3><p>Lorem ipsum dolor sit amet, consectetur adipiscing elit, sed do eiusmod tempor incididunt ut labore</p></div>
  <div class="abs card" style="left:453px;top:583px"><div class="ph" role="img" aria-label="Offshore oil platform at dusk" style="background:linear-gradient(180deg,#3e7dbb,#c99a4a 60%,#2d5f86)"></div><h3>NPI &amp; Facilities Maintenance Services</h3><p>Lorem ipsum dolor sit amet, consectetur adipiscing elit, sed do eiusmod tempor incididunt ut labore</p></div>
  <div class="abs card" style="left:792px;top:583px"><div class="ph" role="img" aria-label="Engineer with tablet inspecting pipework" style="background:linear-gradient(135deg,#a77c6c,#5b6d80 55%,#8a6a5c)"></div><h3>In-House Specialist Coatings</h3><p>Lorem ipsum dolor sit amet, consectetur adipiscing elit, sed do eiusmod tempor incididunt ut labore</p></div>
  <div class="abs pill" style="left:114px;top:996px;width:285px;height:43px;font-weight:500">Contact Us For A Free Quote
    <svg width="12" height="12" viewBox="0 0 12 12"><circle cx="6" cy="6" r="6" fill="#fff"/><path d="M5 3l3 3-3 3" stroke="#555b61" stroke-width="1.8" fill="none"/></svg></div>
</section>

<section class="abs clients">
  <h2 class="heading" style="font-size:37px;margin-top:68px">Our Clients</h2>
  <p style="width:720px;margin:38px auto 0;font-size:13.5px;line-height:30px">Lorem ipsum dolor sit amet, consectetur adipiscing elit, sed do eiusmod tempor incididunt ut labore et dolore magna aliqua. Ut enim ad minim veniam, quis nostrud exercitation ullamco laboris nisi ut aliquip ex ea commodo consequat. Duis aute irure dolor in reprehenderit in voluptate velit esse cillum dolore eu fugiat nulla pariatur.</p>
  <p style="margin-top:18px;font-size:13.5px">— Hannah from Perth</p>
  <div class="abs arrow" style="left:31px;top:167px">&#8249;</div>
  <div class="abs arrow" style="left:1102px;top:167px">&#8250;</div>
</section>

<section>
  <h2 class="abs heading section-title" style="left:0;width:1200px;text-align:center;top:2747px">Our Work</h2>
  <div class="tile" role="img" aria-label="Power plant chimneys at sunset" style="left:88px;top:2822px;width:241px;height:269px;background:linear-gradient(180deg,#6c8fb6,#4b4f5a 60%,#c98a4a)"></div>
  <div class="tile" role="img" aria-label="Orange excavator on a hillside" style="left:345px;top:2822px;width:240px;height:269px;background:linear-gradient(135deg,#7c9ab0,#c8562e 55%,#6b5a45)"></div>
  <div class="tile" role="img" aria-label="Close-up of brake disc being machined" style="left:603px;top:2822px;width:240px;height:269px;background:linear-gradient(135deg,#1d4f7e,#3f86b6 50%,#b56b3e)"></div>
  <div class="tile" role="img" aria-label="Group of engineers in hard hats at a shipyard" style="left:860px;top:2822px;width:240px;height:269px;background:linear-gradient(180deg,#8aa3bb,#3b4d6a 60%,#6f7480)"></div>
  <div class="tile" role="img" aria-label="Worker guiding stacked steel pipes" style="left:88px;top:3107px;width:241px;height:270px;background:linear-gradient(135deg,#6f8f4a,#2f6aa0 55%,#d96a2a)"></div>
  <div class="tile" role="img" aria-label="Workers in a large industrial plant hall" style="left:345px;top:3107px;width:498px;height:270px;background:linear-gradient(135deg,#2f6f7d,#4b5b62 50%,#b5553a)"></div>
  <div class="tile" role="img" aria-label="Large steel pipes in a workshop" style="left:860px;top:3107px;width:240px;height:270px;background:linear-gradient(135deg,#a8aeb4,#4a4340 55%,#c4623a)"></div>
</section>

<footer class="abs footer">
  <div class="abs brand" style="left:153px;top:86px"><div class="dot"></div><div>KWR<small>MAINTENANCE</small></div></div>
  <h4 style="left:364px">LOCATION</h4>
  <div class="list" style="left:364px;top:128px">Lorem ipsum dolor sit amet,<br>consectetur adipiscing elit,<br>sed do eiusmod tempor</div>
  <h4 style="left:656px">CONTACT</h4>
  <div class="list" style="left:656px;top:130px">
    <div style="display:flex;align-items:center;gap:12px"><svg width="22" height="22" viewBox="0 0 30 30"><circle cx="15" cy="15" r="15" fill="#fff"/><path d="M10 9c1-1 2-1 2.5 0l1.2 2c.4.7 0 1.3-.6 1.7-.4.3-.3.8 0 1.3 1 1.5 1.8 2.3 3.2 3.2.5.3 1 .4 1.3 0 .4-.6 1-1 1.7-.6l2 1.2c1 .5 1 1.5 0 2.5-2 2-5 .5-8-2.5s-4.5-6-2.5-8.3z" fill="#000"/></svg>+1 (5550) 555 555</div>
    <div style="display:flex;align-items:center;gap:12px;margin-top:10px"><svg width="22" height="22" viewBox="0 0 22 22"><circle cx="11" cy="11" r="11" fill="#fff"/><rect x="6" y="7.5" width="10" height="7" fill="none" stroke="#000" stroke-width="1.4"/><path d="M6 8l5 4 5-4" fill="none" stroke="#000" stroke-width="1.4"/></svg>info@kwrmaintenance.com</div>
  </div>
  <h4 style="left:981px">QUICK LINKS</h4>
  <div class="list" style="left:981px;top:128px">Home<br>Service<br>About<br>Contact</div>
  <p class="abs" style="left:0;width:1200px;text-align:center;top:258px;font-size:12.5px">Copyright@2024 - All Rights Reserved by Kwr Services</p>
</footer>

</body>
</html>
```